Business Cards Needed for Innovative Healthcare Marketing Company

We are a marketing company focused on healthcare. Our company is all about rebranding yourself renewing your image and generating results. The phoenix stands for "reborn" or "rising" which we provide new brands for our clients we take their old brands and renew it with creativity and innovation. I am looking for a business card with color dimension. I have attached an example of a card I think has the look and feel of what I am trying to accomplish. I like that the card example has black and grey font colors, I like the font placement and the small logo, I really like the use of the colors on the right those are the colors of my logo. My logo is phoenix so maybe incorporating flames similar to that design. I would like the back a solid color maybe red with an opaque version of the logo and website. As a marketing company I am always open to creative liberty!

Target Market(s)

Doctors and business professionals.

Industry/Entity Type

Marketing

Contact Information for Business Card

Valcorne Health Care Marketing
Marla Tenwick- CEO
#(512)638-2974
email-marla@valcorne.com
website- valcorne.com

Font styles to use
Sans Serif

Colors
ec1f27
f37122
ffc214
fbed22
fbf289
f04a50

Requirements
Must have
• The logo and required information
Nice to have
• icons by the information
Should not have
• child like font

```html
<!DOCTYPE html>
<html lang="en">
<head>
<meta charset="utf-8">
<title>Valcorne Health Care Marketing – Business Cards</title>
<link rel="stylesheet" href="https://fonts.googleapis.com/css2?family=Open+Sans:wght@300;400;600;700&display=swap">
<style>
  :root {
    --bg: #ecebe8;
    --card-white: #ffffff;
    --brand-red: #a3201f;
    --brand-orange: #f0901e;
    --accent-orange: #e8711c;
    --text-grey: #3a3a3a;
    --gradient-top: #f39323;
    --gradient-bottom: #a8221f;
    --shadow: rgba(0, 0, 0, 0.18);
  }
  * { box-sizing: border-box; margin: 0; padding: 0; }
  html, body {
    width: 1200px; height: 900px; overflow: hidden;
    background: var(--bg);
    font-family: "Open Sans", Arial, sans-serif;
  }
  .canvas { position: relative; width: 1200px; height: 900px; }

  .card {
    position: absolute;
    width: 560px; height: 320px;
    box-shadow: 0 6px 18px var(--shadow);
    overflow: hidden;
  }

  /* Back of card */
  .card-back {
    left: 590px; top: 90px;
    background: linear-gradient(to bottom, var(--gradient-top) 0%, #d8621f 45%, var(--gradient-bottom) 100%);
    color: #fff;
  }
  .card-back .wordmark {
    position: absolute; left: 0; right: 0; top: 108px;
    text-align: center;
  }
  .card-back .wordmark-name {
    font-weight: 300; font-size: 62px; letter-spacing: 6px; line-height: 1;
  }
  .card-back .wordmark-tagline {
    display: inline-block; margin-top: 8px; padding-top: 6px;
    border-top: 1px solid rgba(255,255,255,0.8);
    font-weight: 300; font-size: 20px; letter-spacing: 3px;
  }

  /* Front of card */
  .card-front {
    left: 60px; top: 480px;
    background: var(--card-white);
  }
  .card-front .decor { position: absolute; inset: 0; }
  .card-front .identity { position: absolute; left: 74px; top: 26px; }
  .card-front .person-name {
    color: var(--accent-orange); font-weight: 700; font-size: 17px;
  }
  .card-front .person-role {
    color: var(--text-grey); font-size: 12px; font-weight: 400; margin-top: -1px;
  }
  .card-front .contact-list {
    position: absolute; left: 30px; top: 148px; list-style: none;
    color: var(--text-grey); font-size: 14px; line-height: 20px;
  }
  .card-front .contact-list li { display: flex; align-items: center; gap: 8px; }
  .card-front .contact-list svg { width: 11px; height: 11px; flex: none; }
  .card-front .wordmark {
    position: absolute; right: 40px; top: 150px; text-align: left;
    color: var(--brand-red);
  }
  .card-front .wordmark-name {
    font-weight: 300; font-size: 40px; letter-spacing: 3px; line-height: 1;
  }
  .card-front .wordmark-tagline {
    margin-top: 4px; padding-top: 3px;
    border-top: 1px solid var(--brand-red);
    font-weight: 300; font-size: 12px; letter-spacing: 1.8px;
  }
</style>
</head>
<body>
<main class="canvas">

  <section class="card card-back" aria-label="Business card back">
    <div class="wordmark">
      <div class="wordmark-name">VALCORNE</div><br>
      <div class="wordmark-tagline">HEALTH CARE MARKETING</div>
    </div>
  </section>

  <section class="card card-front" aria-label="Business card front">
    <svg class="decor" viewBox="0 0 560 320" aria-hidden="true">
      <polygon points="18,28 40,28 28,48 18,48" fill="var(--brand-orange)"/>
      <polygon points="44,28 62,28 52,48 26,48" fill="var(--brand-red)"/>
      <polygon points="0,238 290,238 280,258 0,258" fill="var(--brand-orange)"/>
      <polygon points="296,262 560,262 560,300 276,300" fill="var(--brand-red)"/>
    </svg>

    <div class="identity">
      <div class="person-name">Marla Tenwick</div>
      <div class="person-role">CEO</div>
    </div>

    <ul class="contact-list">
      <li>
        <svg viewBox="0 0 12 12"><path d="M2.5 1h2l1 3-1.3 1a7 7 0 0 0 2.8 2.8l1-1.3 3 1v2A1.5 1.5 0 0 1 9.5 11 8.5 8.5 0 0 1 1 2.5 1.5 1.5 0 0 1 2.5 1z" fill="var(--accent-orange)"/></svg>
        (512)638-2974
      </li>
      <li>
        <svg viewBox="0 0 12 12"><rect x="1" y="2.5" width="10" height="7" fill="var(--accent-orange)"/><path d="M1 2.5 6 6.5 11 2.5" stroke="#fff" stroke-width="1" fill="none"/></svg>
        marla@valcorne.com
      </li>
      <li>
        <svg viewBox="0 0 12 12"><circle cx="6" cy="6" r="5" fill="var(--accent-orange)"/><path d="M1 6h10M6 1c-2 3-2 7 0 10M6 1c2 3 2 7 0 10" stroke="#fff" stroke-width="0.8" fill="none"/></svg>
        valcorne.com
      </li>
    </ul>

    <div class="wordmark">
      <div class="wordmark-name">VALCORNE</div>
      <div class="wordmark-tagline">HEALTH CARE MARKETING</div>
    </div>
  </section>

</main>
</body>
</html>
```